TALMORK

The business want a professional looking business card. We have a scetch we will add but want the extra upgrade, and would like more suggestions for variations of our business cards.

```html
<!DOCTYPE html>
<html lang="en">
<head>
<meta charset="UTF-8">
<title>TALMORK – Business Card</title>
<link rel="stylesheet" href="https://fonts.googleapis.com/css2?family=Cinzel:wght@500&family=Marcellus&family=Roboto:wght@400;500&display=swap">
<style>
  :root {
    --page: #ffffff;
    --card: #000000;
    --gold: #c8a96a;
    --gold-light: #e2cc93;
    --gold-deep: #a88a4e;
  }
  * { margin: 0; padding: 0; box-sizing: border-box; }
  html, body {
    width: 1200px;
    height: 1200px;
    overflow: hidden;
    background: var(--page);
  }
  .sheet {
    position: relative;
    width: 1200px;
    height: 1200px;
  }
  .card {
    position: absolute;
    left: 189px;
    width: 829px;
    height: 497px;
    background: var(--card);
    color: var(--gold);
  }
  .card--front { top: 78px; }
  .card--back { top: 634px; }

  /* Front */
  .brand {
    position: absolute;
    left: 0;
    right: 0;
    top: 196px;
    text-align: center;
  }
  .brand__name {
    font-family: "Cinzel", serif;
    font-weight: 500;
    font-size: 58px;
    line-height: 1;
    letter-spacing: 0.32em;
    padding-left: 0.32em;
    color: var(--gold);
  }
  .brand__since {
    margin-top: 26px;
    font-family: "Roboto", sans-serif;
    font-weight: 500;
    font-size: 19px;
    letter-spacing: 0.75em;
    padding-left: 0.75em;
    color: var(--gold);
  }

  /* Back */
  .person {
    position: absolute;
    left: 125px;
    top: 50px;
  }
  .person__name {
    font-family: "Marcellus", serif;
    font-size: 60px;
    line-height: 1;
    letter-spacing: 0.01em;
    color: var(--gold);
  }
  .person__role {
    margin-top: 16px;
    font-family: "Roboto", sans-serif;
    font-size: 37px;
    line-height: 1;
    color: var(--gold);
  }
  .contacts {
    position: absolute;
    left: 125px;
    top: 280px;
    list-style: none;
  }
  .contact {
    display: flex;
    align-items: center;
    height: 58px;
  }
  .contact__icon {
    width: 36px;
    height: 40px;
    margin-right: 27px;
    fill: none;
    stroke: var(--gold);
    stroke-width: 2.4;
  }
  .contact__text {
    font-family: "Roboto", sans-serif;
    font-size: 40px;
    line-height: 1;
    color: var(--gold);
    background: linear-gradient(90deg, var(--gold-deep), var(--gold-light) 60%, var(--gold));
    -webkit-background-clip: text;
    background-clip: text;
    -webkit-text-fill-color: transparent;
  }
</style>
</head>
<body>
<main class="sheet">
  <section class="card card--front">
    <div class="brand">
      <div class="brand__name">TALMORK</div>
      <div class="brand__since">SINCE 2026</div>
    </div>
  </section>

  <section class="card card--back">
    <div class="person">
      <h1 class="person__name">Henrik Aasmund Solberg</h1>
      <p class="person__role">CEO &amp; FOUNDER</p>
    </div>
    <ul class="contacts">
      <li class="contact">
        <svg class="contact__icon" viewBox="0 0 36 40" aria-hidden="true">
          <rect x="8" y="2" width="20" height="36" rx="3"/>
          <line x1="15" y1="5.5" x2="21" y2="5.5"/>
          <line x1="8" y1="30" x2="28" y2="30"/>
          <circle cx="18" cy="34" r="1.2" fill="currentColor"/>
        </svg>
        <span class="contact__text">004791546270</span>
      </li>
      <li class="contact">
        <svg class="contact__icon" viewBox="0 0 36 40" aria-hidden="true">
          <rect x="1" y="7" width="34" height="25"/>
          <polyline points="1,7 18,22 35,7"/>
          <line x1="1" y1="32" x2="14" y2="19"/>
          <line x1="35" y1="32" x2="22" y2="19"/>
        </svg>
        <span class="contact__text">talmork.llc@postmail.com</span>
      </li>
      <li class="contact">
        <svg class="contact__icon" viewBox="0 0 36 40" aria-hidden="true">
          <circle cx="18" cy="20" r="16"/>
          <ellipse cx="18" cy="20" rx="7" ry="16"/>
          <line x1="18" y1="4" x2="18" y2="36"/>
          <line x1="2" y1="20" x2="34" y2="20"/>
          <line x1="4.5" y1="12" x2="31.5" y2="12"/>
          <line x1="4.5" y1="28" x2="31.5" y2="28"/>
        </svg>
        <span class="contact__text">www.talmork.llc</span>
      </li>
    </ul>
  </section>
</main>
</body>
</html>
```